Looking for business card/letterhead/email signature

Take existing logo and create full design suite of collateral

Contact Information for Business Card

Use mock details that can be edited by us

Font styles to use
Sans Serif

```html
<!DOCTYPE html>
<html lang="en">
<head>
<meta charset="utf-8">
<title>Harlow Digital – Stationery Suite</title>
<link href="https://fonts.googleapis.com/css2?family=Lato:wght@400;700&display=swap" rel="stylesheet">
<style>
:root{
  --navy:#0b4a87;
  --lime:#c2d143;
  --pink:#dc2a73;
  --sky:#2a9fd8;
  --orange:#e8841f;
  --paper:#ececec;
  --ink:#5a5a5a;
  --backdrop:#e3e4e6;
}
*{margin:0;padding:0;box-sizing:border-box}
html,body{width:1200px;height:940px;overflow:hidden}
body{background:var(--backdrop);font-family:'Lato',sans-serif;position:relative;color:var(--ink)}
.piece{position:absolute;overflow:hidden;box-shadow:0 2px 8px rgba(0,0,0,.18)}
.accent-band{position:absolute;top:0;bottom:0;background:linear-gradient(180deg,var(--pink),var(--sky) 55%,var(--lime))}
.logo-panel{position:absolute;top:0;bottom:0;right:0;background:var(--paper)}
.wordmark{font-family:'Lato',sans-serif;font-weight:700;color:var(--navy);line-height:1;text-align:center;position:absolute}
.wordmark.light{color:#fff}
.flag{position:absolute;left:0;width:0;height:0;border-top:9px solid transparent;border-bottom:9px solid transparent;border-left:8px solid var(--lime)}
.ico{width:7px;height:7px;vertical-align:-1px;margin-right:3px;fill:none;stroke:currentColor;stroke-width:1.4}

/* business card front */
.card-front{left:226px;top:70px;width:286px;height:175px;background:var(--navy)}
.card-front .details{position:absolute;left:20px;top:40px;color:#fff}
.card-front .name{color:var(--lime);font-weight:700;font-size:10px;line-height:1.1}
.card-front .role{font-size:6.5px;margin-bottom:11px}
.card-front .addr{font-size:6.2px;line-height:1.35;margin-bottom:11px}
.card-front .contacts{font-size:6.2px;line-height:1.4;list-style:none}
.card-front .accent-band{left:150px;width:12px}
.card-front .logo-panel{left:162px}
.card-front .wordmark{left:162px;right:0;top:70px;font-size:18px}
.card-front .flag{top:44px}

/* business card back */
.card-back{left:226px;top:290px;width:286px;height:175px;background:var(--navy)}
.card-back .wordmark{left:0;right:0;top:73px;font-size:28px}

/* email signature */
.signature{left:74px;top:510px;width:438px;height:134px;background:var(--navy)}
.signature .details{position:absolute;left:26px;top:19px;color:#fff}
.signature .name{color:var(--lime);font-weight:700;font-size:13.5px;line-height:1.1}
.signature .role{font-size:11.5px;margin-bottom:8px}
.signature .contacts{list-style:none;font-size:11.5px;line-height:1.17}
.signature .contacts .ico{width:9px;height:9px;margin-right:5px}
.signature .social{position:absolute;left:194px;top:23px;display:flex;gap:4px}
.signature .social span{width:15px;height:15px;border-radius:50%;background:var(--lime)}
.signature .accent-band{left:334px;width:12px}
.signature .logo-panel{left:346px}
.signature .wordmark{left:346px;right:0;top:46px;font-size:21px}
.signature .flag{top:20px;border-top-width:11px;border-bottom-width:11px;border-left-width:11px}

/* letterhead */
.letterhead{left:561px;top:71px;width:564px;height:798px;background:var(--paper)}
.letterhead .wordmark{left:40px;top:40px;font-size:24px;text-align:left}
.letterhead .head-contacts{position:absolute;left:298px;top:33px;font-size:9.4px;line-height:1.22;list-style:none}
.letterhead .head-address{position:absolute;left:426px;top:45px;font-size:9.4px;line-height:1.22}
.letter{position:absolute;left:62px;top:184px;width:440px;font-size:8.8px;line-height:11.4px}
.letter .date{margin-bottom:22px}
.letter .salutation{margin-bottom:11px}
.letter p.body{text-align:justify;margin-bottom:11px}
.letter .closing{margin-top:15px}
.letter .sign-mark{width:110px;height:24px;margin:6px 0 4px;background:linear-gradient(90deg,rgba(90,90,90,.18),rgba(90,90,90,.05))}
.letterhead .footer-band{position:absolute;left:0;right:0;bottom:0;height:120px;background:linear-gradient(180deg,rgba(220,42,115,.35),var(--sky) 40%,var(--navy))}
</style>
</head>
<body>
<svg width="0" height="0" style="position:absolute" aria-hidden="true">
  <symbol id="i-phone" viewBox="0 0 10 10"><path d="M2 1l2 2-1 1.5c.7 1.3 1.3 2 2.5 2.5L7 6l2 2-1.5 1.5C5 9 1 5 .5 2.5z"/></symbol>
  <symbol id="i-mobile" viewBox="0 0 10 10"><rect x="2.5" y=".8" width="5" height="8.4" rx=".8"/></symbol>
  <symbol id="i-mail" viewBox="0 0 10 10"><rect x=".8" y="2" width="8.4" height="6"/><path d="M.8 2L5 5.5 9.2 2"/></symbol>
  <symbol id="i-web" viewBox="0 0 10 10"><circle cx="5" cy="5" r="4"/><path d="M1 5h8M5 1c-2 2.5-2 5.5 0 8M5 1c2 2.5 2 5.5 0 8"/></symbol>
</svg>

<section class="piece card-front" aria-label="Business card front">
  <div class="accent-band" role="img" aria-label="Decorative colour arcs in brand tones"></div>
  <div class="logo-panel"></div>
  <span class="flag"></span>
  <div class="details">
    <div class="name">Nora K. Harlow</div>
    <div class="role">Managing Director</div>
    <div class="addr">Co.Street, Building/Suite<br>City/State, Zip Code</div>
    <ul class="contacts">
      <li><svg class="ico"><use href="#i-phone"/></svg>555.214.3870</li>
      <li><svg class="ico"><use href="#i-mobile"/></svg>555.214.3871</li>
      <li><svg class="ico"><use href="#i-mail"/></svg>info@harlow-digital.com</li>
      <li><svg class="ico"><use href="#i-web"/></svg>www.harlow-digital.com</li>
    </ul>
  </div>
  <div class="wordmark">Harlow<br>Digital</div>
</section>

<section class="piece card-back" aria-label="Business card back">
  <div class="wordmark light">Harlow Digital</div>
</section>

<section class="piece signature" aria-label="Email signature">
  <div class="accent-band" role="img" aria-label="Decorative colour arcs in brand tones"></div>
  <div class="logo-panel"></div>
  <span class="flag"></span>
  <div class="details">
    <div class="name">Nora K. Harlow</div>
    <div class="role">Managing Director</div>
    <ul class="contacts">
      <li><svg class="ico"><use href="#i-phone"/></svg>555.214.3870</li>
      <li><svg class="ico"><use href="#i-mobile"/></svg>555.214.3871</li>
      <li><svg class="ico"><use href="#i-mail"/></svg>info@harlow-digital.com</li>
      <li><svg class="ico"><use href="#i-web"/></svg>www.harlow-digital.com</li>
      <li>Co.Street, Building/Suite, City/State, Zip Code</li>
    </ul>
  </div>
  <div class="social" aria-label="Social links"><span></span><span></span><span></span></div>
  <div class="wordmark">Harlow<br>Digital</div>
</section>

<section class="piece letterhead" aria-label="Letterhead">
  <div class="wordmark">Harlow<br>Digital</div>
  <ul class="head-contacts">
    <li><svg class="ico"><use href="#i-phone"/></svg>555.214.3870</li>
    <li><svg class="ico"><use href="#i-mobile"/></svg>555.214.3871</li>
    <li><svg class="ico"><use href="#i-mail"/></svg>info@harlow-digital.com</li>
    <li><svg class="ico"><use href="#i-web"/></svg>www.harlow-digital.com</li>
  </ul>
  <div class="head-address">Harlow Digital<br>Co.Street, Building/Suite<br>City/State, Zip Code</div>

  <article class="letter">
    <p class="date">January 01, 2020</p>
    <p class="salutation">Dear Marcus Feldner,</p>
    <p class="body">Lorem ipsum dolor sit amet, consectetuer adipiscing elit, sed diam nonummy nibh euismod tincidunt ut laoreet dolore magna aliquam erat volutpat. Ut wisi enim ad minim veniam, quis nostrud exerci tation ullamcorper suscipit lobortis nisl ut aliquip ex ea commodo consequat. Duis dolore te feugait nulla facilisi. Nam liber tempor cum soluta nobis eleifend option congue nihil imperdiet doming id quod mazim placerat facer possim assum. Duis autem vel eum iriure dolor in hendrerit in vulputate velit esse molestie consequat, vel illum dolore eu feugiat nulla facilisis at vero eros et accumsan et iusto odio dignissim qui blandit praesent luptatum zzril delenit augue duis dolore te feugait nulla facilisi. Consectetuer adipiscing elit, sed diam nonummy nibh euismod tincidunt ut laoreet dolore magna aliquam erat volutpat. Ut wisi enim ad minim veniam, quis nostrud exerci tation ullamcorper suscipit lobortis nisl ut aliquip ex ea commodo consequat.</p>
    <p class="body">Consectetuer adipiscing elit, sed diam nonummy nibh euismod tincidunt ut laoreet dolore magna aliquam erat volutpat. Ut wisi enim ad minim veniam, quis nostrud exerci tation ullamcorper suscipit lobortis nisl ut aliquip ex ea commodo consequat. Consectetuer adipiscing elit, sed diam nonummy nibh euismod tincidunt ut laoreet dolore magna aliquam erat volutpat. Ut wisi enim ad minim veniam, quis nostrud exerci tation ullamcorper suscipit lobortis nisl ut aliquip ex ea commodo consequat.</p>
    <p class="body">Dolor sit amet, consectetuer adipiscing elit, sed diam nonummy nibh euismod tincidunt ut laoreet dolore magna aliquam erat volutpat. Ut wisi enim ad minim veniam, quis nostrud exerci tation ullamcorper suscipit lobortis nisl ut aliquip ex ea commodo consequat. Duis dolore te feugait nulla facilisi. Nam liber tempor cum soluta nobis eleifend option congue nihil imperdiet doming id quod mazim placerat facer possim assum. Duis dolore te feugait nulla facilisi. Nam liber tempor cum soluta nobis eleifend option congue nihil imperdiet doming id quod mazim placerat facer possim assum. Duis dolore te feugait nulla facilisi. Nam liber tempor cum soluta nobis eleifend option congue nihil imperdiet doming id quod mazim placerat facer possim assum.</p>
    <p class="closing">Sincerely Yours,</p>
    <div class="sign-mark" role="img" aria-label="Handwritten signature of Thomas Verlan"></div>
    <p>Authorized Managing Director<br>Your Company Name</p>
  </article>

  <div class="footer-band" role="img" aria-label="Decorative colour waves in brand tones"></div>
</section>
</body>
</html>
```